4D Cradle Glimpse Luxury Ultrasound Billboard

Design a HIGH-END, MODERN billboard for my private prenatal ultrasound studio, 4D Cradle Glimpse, located in Pace, Florida.
This billboard will be viewed by drivers traveling at highway speeds, so it must be extremely clean, simple, and readable within 6 seconds.
About My Business
4D Cradle Glimpse is a private prenatal ultrasound studio specializing in:
Highest technology 4D/HD Ultrasounds
Early Gender Determination
Pregnancy Confirmation
I have been serving families for nearly 10 years and is known for creating a memorable experience, not just an ultrasound appointment.
Design Style
I DO NOT want:
Flowers
Leaves
Swirls
Glitter
Hearts everywhere
Busy backgrounds
Generic maternity stock graphics
I DO want:
Modern
Luxury
Upscale
Clean
Professional
Eye-catching
Premium medical spa feel
Colors
Use colors from my logo:
LOGO Green ( or a deep green)
Black
White
Soft Gold accents
Images:
Incorporate my professional headshot in a clean, modern way, logo, and the ultrasound images
Text
Keep wording minimal.
Primary Headline ( OPEN TO IDEAS) :
EXAMPLES ( WOULD RATHER SOMETHING MORE CATCHY)
" ADVANCED IMAGING. UNFORGETTABLE MOMENTS"
"MEET YOUR BABY BEFORE BIRTH"
Under headline:
4D Ultrasound • Early Gender • Pregnancy Confirmation
Business Name:
4D Cradle Glimpse
Private Prenatal Ultrasound Studio
Phone Number:
850-471-5923
Important
This billboard must be readable in 5–6 seconds from a moving vehicle.
Less text is better.
The phone number and business name must be visible from a distance.
The design should feel like a premium brand that immediately tells expecting parents:
“This is where I go to see my baby.”
Files Provided
Official logo
Headshot
Ultrasound images
Don’t make this look like a medical office billboard.
Make it look like a luxury baby experience billboard. That’s what separates 4D Cradle Glimpse from hospitals, OB offices, and all the new studios popping up around you. The emotional connection is what gets moms to book. ❤️
Billboard Size - 10.6” x 36”

```html
<!DOCTYPE html>
<html lang="en">
<head>
<meta charset="utf-8">
<title>4D Cradle Glimpse Billboard</title>
<link rel="stylesheet" href="https://fonts.googleapis.com/css2?family=Abril+Fatface&family=Oswald:wght@600&family=Poppins:wght@500;600;700&display=swap">
<style>
  :root {
    --page: #e9e7e2;
    --board: #f5f4f0;
    --green: #1f2d24;
    --green-deep: #2b3a2e;
    --gold: #d9a53a;
    --gold-soft: #e3b658;
    --white: #ffffff;
  }
  * { margin: 0; padding: 0; box-sizing: border-box; }
  html, body { width: 1200px; height: 829px; overflow: hidden; background: var(--page); }
  .billboard {
    position: absolute; left: 20px; top: 243px;
    width: 1160px; height: 342px;
    background: var(--board);
    overflow: hidden;
    box-shadow: 0 6px 18px rgba(0,0,0,.12);
  }
  .brand {
    position: absolute; left: 230px; top: 24px; width: 300px;
    text-align: center; color: var(--green);
  }
  .brand-name {
    display: flex; align-items: center; justify-content: center; gap: 8px;
    font-family: "Poppins", sans-serif; font-weight: 700; font-size: 22px; color: var(--gold);
  }
  .brand-dot { width: 12px; height: 12px; border-radius: 50%; background: var(--gold); }
  .brand-rule { display: block; width: 170px; height: 1px; background: var(--gold); margin: 6px auto 6px; }
  .brand-tag { font-family: "Poppins", sans-serif; font-weight: 600; font-size: 12.5px; letter-spacing: .2px; }
  .headline {
    position: absolute; left: 40px; top: 94px;
    font-family: "Abril Fatface", serif; font-size: 66px; line-height: 1;
    color: var(--green); letter-spacing: .5px; white-space: nowrap;
  }
  .services {
    position: absolute; left: 42px; top: 176px;
    font-family: "Poppins", sans-serif; font-weight: 600; font-size: 19px;
    color: var(--green); white-space: nowrap;
  }
  .contact { position: absolute; left: 150px; top: 220px; display: flex; align-items: center; gap: 20px; }
  .phone-icon { width: 40px; height: 40px; }
  .phone-number {
    font-family: "Oswald", sans-serif; font-weight: 600; font-size: 64px; line-height: 1;
    color: var(--green); letter-spacing: 1px;
  }
  .feature { position: absolute; left: 0; top: 0; width: 1160px; height: 342px; }
</style>
</head>
<body>
<main class="billboard">
  <svg class="feature" viewBox="0 0 1160 342" aria-hidden="false">
    <defs>
      <radialGradient id="scanTone" cx="50%" cy="50%" r="55%">
        <stop offset="0" stop-color="#6b2a1c"/>
        <stop offset="0.35" stop-color="#c9664a"/>
        <stop offset="0.8" stop-color="#e59a80"/>
        <stop offset="1" stop-color="#f3d6cc"/>
      </radialGradient>
      <linearGradient id="portraitTone" x1="0" y1="0" x2="0" y2="1">
        <stop offset="0" stop-color="#cdbb92"/>
        <stop offset="0.45" stop-color="#d8c6b4"/>
        <stop offset="1" stop-color="#3c4a3b"/>
      </linearGradient>
    </defs>
    <rect class="gold-panel" x="860" y="0" width="300" height="342" fill="var(--gold)"/>
    <circle class="gold-disc" cx="860" cy="185" r="190" fill="var(--gold)"/>
    <circle class="scan-frame" cx="830" cy="180" r="142" fill="var(--white)" opacity=".92"/>
    <circle class="scan-ring" cx="830" cy="180" r="132" fill="none" stroke="var(--gold)" stroke-width="2"/>
    <circle cx="830" cy="180" r="124" fill="url(#scanTone)" role="img" aria-label="4D ultrasound image of twins"/>
    <rect x="915" y="62" width="245" height="280" fill="url(#portraitTone)" role="img" aria-label="Headshot of the studio sonographer seated beside an ultrasound machine"/>
  </svg>

  <div class="brand">
    <div class="brand-name"><span class="brand-dot"></span>4D Cradle Glimpse</div>
    <span class="brand-rule"></span>
    <div class="brand-tag">Private Prenatal Ultrasound Studio</div>
  </div>

  <h1 class="headline">MEET YOUR BABY</h1>
  <p class="services">• 4D Ultrasound • Early Gender • Pregnancy Confirmation</p>

  <div class="contact">
    <svg class="phone-icon" viewBox="0 0 40 40" aria-hidden="true">
      <circle cx="20" cy="20" r="20" fill="var(--gold)"/>
      <path d="M14 11c1-.6 2-.4 2.6.5l2 3c.5.8.3 1.7-.4 2.3l-1.3 1c.9 2 2.5 3.6 4.5 4.6l1-1.3c.6-.7 1.6-.9 2.3-.4l3 2c.9.6 1.1 1.7.5 2.6l-1 1.5c-.8 1.2-2.3 1.7-3.7 1.2-5.5-2-9.5-6-11.5-11.5-.5-1.4 0-2.9 1.2-3.7z" fill="var(--green)"/>
    </svg>
    <span class="phone-number">850 471 5923</span>
  </div>
</main>
</body>
</html>
```